Postcard Design

Hi thereI would like a simple postcard for my online kids clothing and decor business. The brand colours are black, white and gold. I want enough white space so I can write personal messages. The logo to be placed at the top and with gold stars scattered around the outside. At the bottom of the card in the middle I want website, facebook page and instragram page. Take a look at the example postcard attached to get a good feel of my requirements. website is www.jaxonrose.comFacebook is facebook.com/Jaxon RoseInstagram is @jaxonrose_storeEmail is hello@milbrenvale.com
Industry/Entity Type
Business
Look and feel
Each slider illustrates characteristics of the customer's brand and the style your logo design should communicate.

```html
<!DOCTYPE html>
<html lang="en">
<head>
<meta charset="utf-8">
<title>Milbren Vale Postcard</title>
<link href="https://fonts.googleapis.com/css2?family=Oswald:wght@300;500&display=swap" rel="stylesheet">
<style>
  :root {
    --paper: #ffffff;
    --ink: #111111;
    --ink-soft: #454545;
    --gold: #c9a24a;
    --gold-pale: #ecdcb1;
  }
  html, body {
    margin: 0;
    padding: 0;
    width: 1200px;
    height: 886px;
    overflow: hidden;
    background: var(--paper);
  }
  .postcard {
    position: relative;
    width: 1200px;
    height: 886px;
    background: var(--paper);
    font-family: "Oswald", sans-serif;
    overflow: hidden;
  }
  .star-field {
    position: absolute;
    left: 0;
    width: 1200px;
  }
  .star-field--top {
    top: 0;
    height: 380px;
    background: linear-gradient(to bottom, var(--gold-pale) 0%, rgba(236, 220, 177, 0.55) 45%, rgba(255, 255, 255, 0) 100%);
  }
  .star-field--bottom {
    bottom: 0;
    height: 180px;
    background: linear-gradient(to top, var(--gold-pale) 0%, rgba(236, 220, 177, 0.5) 50%, rgba(255, 255, 255, 0) 100%);
  }
  .brand-name {
    position: absolute;
    top: 70px;
    left: 0;
    width: 1200px;
    margin: 0;
    text-align: center;
    font-weight: 500;
    font-size: 150px;
    line-height: 170px;
    color: var(--ink);
  }
  .website {
    position: absolute;
    top: 662px;
    left: 0;
    width: 1200px;
    margin: 0;
    text-align: center;
    font-weight: 500;
    font-size: 42px;
    line-height: 56px;
    letter-spacing: 0.42em;
    color: var(--ink-soft);
  }
  .contact-list {
    position: absolute;
    top: 750px;
    left: 0;
    width: 1200px;
    margin: 0;
    padding: 0;
    list-style: none;
    display: flex;
    justify-content: center;
    gap: 30px;
    font-weight: 300;
    font-size: 31px;
    line-height: 44px;
    color: var(--ink-soft);
  }
  .contact-item {
    display: flex;
    align-items: center;
    gap: 10px;
  }
  .contact-icon {
    width: 32px;
    height: 32px;
    flex: none;
  }
</style>
</head>
<body>
  <main class="postcard">
    <div class="star-field star-field--top" role="img" aria-label="Scattered gold stars and shooting stars fading down from the top edge"></div>
    <div class="star-field star-field--bottom" role="img" aria-label="Scattered gold stars rising from the bottom edge"></div>

    <h1 class="brand-name">Milbren<br>Vale</h1>

    <p class="website">www.milbrenvale.com</p>

    <ul class="contact-list">
      <li class="contact-item">
        <svg class="contact-icon" viewBox="0 0 34 34" aria-hidden="true"><circle cx="17" cy="17" r="16" fill="#454545"/></svg>
        <span>@milbrenvale_store</span>
      </li>
      <li class="contact-item">
        <svg class="contact-icon" viewBox="0 0 34 34" aria-hidden="true"><circle cx="17" cy="17" r="16" fill="#454545"/></svg>
        <span>kinfolia.com/milbrenvalekids</span>
      </li>
      <li class="contact-item">
        <svg class="contact-icon" viewBox="0 0 34 34" aria-hidden="true">
          <circle cx="17" cy="17" r="16" fill="#454545"/>
          <rect x="9" y="11.5" width="16" height="11" fill="none" stroke="#ffffff" stroke-width="1.8"/>
          <polyline points="9,11.5 17,18 25,11.5" fill="none" stroke="#ffffff" stroke-width="1.8"/>
        </svg>
        <span>hello@milbrenvale.com</span>
      </li>
    </ul>
  </main>
</body>
</html>
```